Bramble firearms training and consulting

Business card for a new firearms training company. I train persons on firearms safety, personal protection, shooting tactics and CHL.Im a Prior State trooper. I also served 4 years in IRaq as a Protection contractor with the Dept of State. Real world training for Real world situations. I would like the company name to be, BRAMBLE FIREARMS TRAINING AND CONSULTING. Im native american also. Ive provided pics. Put the name Bramble above the arrowhead but rotate the arrowhead to the right with it pointing right. Then place bramble inside the arrowhead. lets see both.
Industry/Entity Type
Business
Contact Information for Business Card
Christian Chatellier817-240-0488shadowtraining33@gmail.com

```html
<!DOCTYPE html>
<html lang="en">
<head>
<meta charset="utf-8">
<title>Bramble Firearms Training and Consulting – Business Cards</title>
<link rel="stylesheet" href="https://fonts.googleapis.com/css2?family=Fondamento&family=Montserrat:wght@400&display=swap">
<style>
  :root {
    --backdrop: #1b1b1b;
    --card: #f3f3f2;
    --brand-red: #7a150c;
    --ink: #111111;
  }
  * { box-sizing: border-box; margin: 0; padding: 0; }
  html, body { width: 1200px; height: 1000px; overflow: hidden; }
  body { background: var(--backdrop); position: relative; }

  .card {
    position: absolute;
    top: 200px;
    width: 380px;
    height: 600px;
    background: var(--card);
    font-family: "Fondamento", Georgia, serif;
    color: var(--ink);
  }
  .card--classic { left: 170px; }
  .card--offset { left: 650px; }

  .band { position: absolute; left: 105px; width: 170px; }
  .band__bar { height: 28px; background: var(--brand-red); }
  .band__rule { height: 2px; background: var(--brand-red); }
  .band--top { top: 18px; }
  .band--top .band__rule { margin-top: 4px; }
  .band--bottom { bottom: 18px; }
  .band--bottom .band__rule { margin-bottom: 4px; }

  .brand { position: absolute; left: 0; right: 0; top: 95px; text-align: center; }
  .brand__name {
    font-size: 56px;
    letter-spacing: 4px;
    color: var(--brand-red);
    line-height: 1;
  }
  .brand__tagline {
    margin-top: 26px;
    font-family: "Montserrat", Arial, sans-serif;
    font-size: 13.5px;
    letter-spacing: 0.2px;
    color: var(--brand-red);
  }

  .person { position: absolute; left: 0; right: 0; text-align: center; }
  .card--classic .person { top: 318px; }
  .card--offset .person { top: 340px; }
  .person__name { font-size: 31px; line-height: 1.1; }
  .person__role { font-size: 14px; margin-top: 2px; }

  .contacts { position: absolute; list-style: none; font-size: 15.5px; line-height: 22px; }
  .card--classic .contacts { top: 462px; right: 28px; }
  .card--offset .contacts { top: 478px; left: 30px; }
  .contacts__item { display: flex; align-items: center; gap: 8px; white-space: nowrap; }
  .card--classic .contacts__item { justify-content: flex-end; }
  .contacts__icon { width: 15px; height: 15px; flex: none; }
</style>
</head>
<body>

  <section class="card card--classic" aria-label="Business card, centred layout">
    <div class="band band--top"><div class="band__bar"></div><div class="band__rule"></div></div>
    <div class="brand">
      <div class="brand__name">BRAMBLE</div>
      <div class="brand__tagline">FIREARMS TRAINING AND CONSULTING</div>
    </div>
    <div class="person">
      <div class="person__name">Dorian Pellwick</div>
      <div class="person__role">Trainer and Consultant</div>
    </div>
    <ul class="contacts">
      <li class="contacts__item">
        <svg class="contacts__icon" viewBox="0 0 16 16" aria-hidden="true"><circle cx="8" cy="8" r="7" fill="none" stroke="#111" stroke-width="1.4"/><path d="M5.5 4.5l1.3 0 .6 1.8-.9.7a4.5 4.5 0 0 0 2.5 2.5l.7-.9 1.8.6v1.3c-3.6.3-6.3-2.4-6-6z" fill="#111"/></svg>
        <span>555-317-9062</span>
      </li>
      <li class="contacts__item">
        <svg class="contacts__icon" viewBox="0 0 16 16" aria-hidden="true"><circle cx="8" cy="8" r="7" fill="none" stroke="#111" stroke-width="1.4"/><rect x="4" y="5.5" width="8" height="5" fill="#111"/><path d="M4 5.5l4 3 4-3" stroke="#f3f3f2" stroke-width="0.9" fill="none"/></svg>
        <span>bramblecourse58@mailvento.com</span>
      </li>
      <li class="contacts__item">
        <svg class="contacts__icon" viewBox="0 0 16 16" aria-hidden="true"><circle cx="8" cy="8" r="7" fill="none" stroke="#111" stroke-width="1.4"/><path d="M8 3.8l4 3.4h-1.1v4H5.1v-4H4z" fill="#111"/></svg>
        <span>48 Larkfield Ave, Town, NY 10482</span>
      </li>
    </ul>
    <div class="band band--bottom"><div class="band__rule"></div><div class="band__bar"></div></div>
  </section>

  <section class="card card--offset" aria-label="Business card, left-set contacts layout">
    <div class="band band--top"><div class="band__bar"></div><div class="band__rule"></div></div>
    <div class="brand">
      <div class="brand__name">BRAMBLE</div>
      <div class="brand__tagline">FIREARMS TRAINING AND CONSULTING</div>
    </div>
    <div class="person">
      <div class="person__name">Dorian Pellwick</div>
      <div class="person__role">Trainer and Consultant</div>
    </div>
    <ul class="contacts">
      <li class="contacts__item">
        <svg class="contacts__icon" viewBox="0 0 16 16" aria-hidden="true"><circle cx="8" cy="8" r="7" fill="none" stroke="#111" stroke-width="1.4"/><path d="M5.5 4.5l1.3 0 .6 1.8-.9.7a4.5 4.5 0 0 0 2.5 2.5l.7-.9 1.8.6v1.3c-3.6.3-6.3-2.4-6-6z" fill="#111"/></svg>
        <span>555-317-9062</span>
      </li>
      <li class="contacts__item">
        <svg class="contacts__icon" viewBox="0 0 16 16" aria-hidden="true"><circle cx="8" cy="8" r="7" fill="none" stroke="#111" stroke-width="1.4"/><rect x="4" y="5.5" width="8" height="5" fill="#111"/><path d="M4 5.5l4 3 4-3" stroke="#f3f3f2" stroke-width="0.9" fill="none"/></svg>
        <span>bramblecourse58@mailvento.com</span>
      </li>
      <li class="contacts__item">
        <svg class="contacts__icon" viewBox="0 0 16 16" aria-hidden="true"><circle cx="8" cy="8" r="7" fill="none" stroke="#111" stroke-width="1.4"/><path d="M8 3.8l4 3.4h-1.1v4H5.1v-4H4z" fill="#111"/></svg>
        <span>48 Larkfield Ave, Town, NY 10482</span>
      </li>
    </ul>
    <div class="band band--bottom"><div class="band__rule"></div><div class="band__bar"></div></div>
  </section>

</body>
</html>
```